Bright Harbor Learning Center Brochure Design

We are looking for a visually appealing and well-structured tri-fold brochure that effectively communicates our mission, values, and offerings. The brochure should be engaging, informative, and eye-catching, ensuring that families can easily connect with our message.
Key Requirements:
- Front Cover: Must include our Bright Harbor Learning Center logo and a compelling design that draws attention.
- Back Panel: Should display our locations, social media handles, QR code, website, and phone number, arranged neatly for easy access. (Reference the attached example for layout inspiration.)
- Content & Imagery: The provided text must be incorporated in a clean, organized layout that flows naturally. We’ve also included photos of children we would like used. (Not all photos have to be used, just some)
- Design & Color Scheme: We are open to creative variations, but the overall aesthetic should feel cohesive, professional, and visually engaging. The design should capture the warmth, care, and discovery-based learning environment we provide.
- Attention-Grabbing & Readable: The brochure should be easy to read, with well-balanced text and imagery that doesn’t overwhelm the viewer.
We are excited to see your creative approach—make it stand out while maintaining clarity and professionalism!
---------------------------------------------------------------------------
This is the info that needs to be used:
Welcome to Bright Harbor Learning Center
Where Learning & Care Come Together!
At Bright Harbor, we go beyond childcare—we create a warm, nurturing community where families feel supported and confident in their child’s growth.
✅ Privately owned early learning centers with hands-on leadership
✅ Safe, engaging environments designed to inspire young minds
✅ Now transitioning to a Reggio Emilia-inspired approach—encouraging exploration, creativity, and child-led learning
We are also proud to offer exclusive corporate discounts for professionals in key industries:
🔹 Teachers
🔹 Healthcare & Hospital Staff
🔹 Law Enforcement & First Responders
🔹 Military Families
🔹 Employees of Partnered Businesses & Apartments
Quality childcare should be affordable and accessible—because when families thrive, communities grow!
Our Approach: Learning Through Exploration
At Bright Harbor, we believe that children learn best through curiosity, hands-on discovery, and meaningful experiences. That’s why we are transitioning to a Reggio Emilia-inspired philosophy, where:
✨ Children take the lead – Learning is shaped by their interests and natural curiosity
✨ Teachers are guides – Educators observe, support, and enrich children’s experiences
✨ The environment is a teacher – Classrooms are designed to inspire creativity and exploration
✨ Collaboration is key – Children, families, and educators work together in a connected learning community
We blend this philosophy with The Playwise Framework® for Preschool and Emergent Curriculum to create a research-backed, child-centered learning experience. The Playwise Framework® builds confidence, critical thinking, and academic readiness, while Emergent Curriculum adapts lessons to children's interests—making learning engaging, meaningful, and fun.
Our Mission: Growing Together
🌟 Building strong partnerships – Open communication with families & communities
🌟 Nurturing confidence & creativity – Every child is seen, heard, and supported
🌟 Fostering a lifelong love for learning – Through discovery, exploration & meaningful experiences
As we transition to a Reggio Emilia-inspired approach, we are excited to offer a learning experience that is more engaging, dynamic, and child-centered than ever before.
Imagine a place where every child’s voice is heard, creativity is celebrated, and learning is an adventure—welcome to Bright Harbor!

```html
<!DOCTYPE html>
<html lang="en">
<head>
<meta charset="utf-8">
<title>Bright Harbor Learning Center – Brochure Inside Spread</title>
<link href="https://fonts.googleapis.com/css2?family=Fredoka:wght@600;700&family=Kalam:wght@300;400&family=Arimo:wght@400&display=swap" rel="stylesheet">
<style>
  :root{
    --blue:#3a67b1;
    --blue-deep:#3363ae;
    --sky:#8fb8ea;
    --sky-light:#b9d4f3;
    --mint:#eefbe8;
    --green:#5ab52d;
    --tick:#d8e021;
    --lemon:#e2ea3f;
    --ink:#333333;
    --white:#ffffff;
  }
  *{box-sizing:border-box;margin:0;padding:0}
  html,body{width:1200px;height:848px;overflow:hidden;background:var(--white)}
  .spread{position:relative;width:1200px;height:848px;overflow:hidden}
  .panel{position:absolute;top:0;width:400px;height:848px;overflow:hidden}
  .panel--left{left:0;background:var(--white)}
  .panel--middle{left:400px;background:var(--mint)}
  .panel--right{left:800px;background:var(--blue-deep)}
  .shape{position:absolute;left:0;top:0}
  .display{font-family:"Fredoka",sans-serif;font-weight:700;color:var(--blue);line-height:.98;letter-spacing:-.3px}
  .body-sans{font-family:"Arimo",Arial,sans-serif}
  .script{font-family:"Kalam",cursive;font-weight:300}

  /* left */
  .left-heading{position:absolute;left:26px;top:270px;font-size:29px}
  .left-tagline{position:absolute;left:26px;top:364px;width:360px;font-size:17px;color:var(--green);line-height:1.17}

  /* middle */
  .brand{position:absolute;left:0;top:78px;width:400px;display:flex;align-items:center;justify-content:center;gap:8px}
  .brand-dot{width:18px;height:18px;border-radius:50%;background:var(--green)}
  .brand-name{font-family:"Fredoka",sans-serif;font-weight:700;font-size:22px;color:var(--blue)}
  .mid-heading{position:absolute;left:22px;top:145px;font-size:30.5px}
  .mid-intro{position:absolute;left:22px;top:248px;width:355px;font-size:15.3px;color:var(--green);line-height:1.26;text-align:justify}
  .checklist{position:absolute;list-style:none}
  .checklist li{position:relative;padding-left:27px;font-family:"Fredoka",sans-serif;font-weight:600;font-size:15px;line-height:1.08}
  .checklist li svg{position:absolute;left:0;top:1px;width:24px;height:22px}
  .checklist--approach{left:22px;top:380px;width:356px}
  .checklist--approach li{color:var(--blue);margin-bottom:15px;text-align:justify}
  .mid-closing{position:absolute;left:36px;top:602px;width:328px;font-size:14.2px;color:var(--ink);line-height:1.22;text-align:justify}

  /* right */
  .right-heading{position:absolute;left:22px;top:42px;font-size:30.5px;color:var(--white)}
  .checklist--mission{left:22px;top:120px;width:360px}
  .checklist--mission li{color:var(--white);margin-bottom:15px}
  .right-note{position:absolute;left:22px;top:284px;width:360px;font-size:14.2px;color:var(--white);line-height:1.22}
  .welcome-box{position:absolute;left:13px;top:730px;width:373px;height:88px;border-radius:16px;background:var(--lemon);opacity:.95;padding:14px 14px;font-family:"Fredoka",sans-serif;font-weight:700;font-size:15.3px;line-height:1.1;color:var(--blue);text-align:justify}
</style>
</head>
<body>
<main class="spread">

  <!-- Left panel -->
  <section class="panel panel--left">
    <svg class="shape" width="400" height="848" viewBox="0 0 400 848">
      <defs>
        <linearGradient id="grainTones" x1="0" y1="0" x2="1" y2="1">
          <stop offset="0" stop-color="#c9b7a0"/>
          <stop offset=".55" stop-color="#a88a63"/>
          <stop offset="1" stop-color="#8a6c4a"/>
        </linearGradient>
        <linearGradient id="readingTones" x1="0" y1="0" x2="1" y2="1">
          <stop offset="0" stop-color="#d9c2a2"/>
          <stop offset=".5" stop-color="#c79a72"/>
          <stop offset="1" stop-color="#b56a58"/>
        </linearGradient>
        <linearGradient id="leftCircle" x1="0" y1="0" x2="0" y2="1">
          <stop offset="0" stop-color="#7fb0e2"/>
          <stop offset="1" stop-color="#9ec6ef"/>
        </linearGradient>
      </defs>
      <path d="M0 120 C60 200 110 255 180 258 C250 260 285 200 283 120 C281 60 250 20 230 0 L0 0 Z" fill="var(--sky)"/>
      <path role="img" aria-label="Photo: a child scooping grain in a sensory bin" d="M0 110 C60 190 110 243 178 245 C240 247 275 190 274 118 C272 60 245 20 225 0 L0 0 Z" fill="url(#grainTones)"/>
      <circle cx="395" cy="850" r="385" fill="url(#leftCircle)"/>
      <path role="img" aria-label="Photo: children reading on cushions beside a bookshelf" d="M0 430 L235 400 L250 570 C300 620 330 700 330 848 L0 848 Z" fill="url(#readingTones)"/>
    </svg>
    <h2 class="display left-heading">Quality childcare<br>should be affordable<br>and accessible</h2>
    <p class="body-sans left-tagline">because when families thrive, communities grow!</p>
  </section>

  <!-- Middle panel -->
  <section class="panel panel--middle">
    <svg class="shape" width="400" height="848" viewBox="0 0 400 848">
      <path d="M0 690 C40 800 110 835 200 835 C300 835 370 760 400 650 L400 848 L0 848 Z" fill="var(--sky-light)"/>
    </svg>
    <div class="brand"><span class="brand-dot"></span><span class="brand-name">Bright Harbor</span></div>
    <h1 class="display mid-heading">Our Approach:<br>Learning Through<br>Exploration</h1>
    <p class="body-sans mid-intro">At Bright Harbor, we believe that children learn best through curiosity, hands-on discovery, and meaningful experiences.<br>That’s why we are transitioning to a Reggio Emilia-inspired philosophy, where:</p>
    <ul class="checklist checklist--approach">
      <li><svg viewBox="0 0 24 22"><path d="M2 12 L9 19 L22 3" fill="none" stroke="var(--tick)" stroke-width="4" stroke-linecap="round" stroke-linejoin="round"/></svg>Children take the lead – Learning is shaped by their interests and natural curiosity</li>
      <li><svg viewBox="0 0 24 22"><path d="M2 12 L9 19 L22 3" fill="none" stroke="var(--tick)" stroke-width="4" stroke-linecap="round" stroke-linejoin="round"/></svg>Teachers are guides – Educators observe, support, and enrich children’s experiences</li>
      <li><svg viewBox="0 0 24 22"><path d="M2 12 L9 19 L22 3" fill="none" stroke="var(--tick)" stroke-width="4" stroke-linecap="round" stroke-linejoin="round"/></svg>The environment is a teacher – Classrooms are designed to inspire creativity and exploration</li>
      <li><svg viewBox="0 0 24 22"><path d="M2 12 L9 19 L22 3" fill="none" stroke="var(--tick)" stroke-width="4" stroke-linecap="round" stroke-linejoin="round"/></svg>Collaboration is key – Children, families, and educators work together in a connected learning community</li>
    </ul>
    <p class="script mid-closing">We blend this philosophy with The Playwise Framework® for Preschool and Emergent Curriculum to create a research-backed, child-centered learning experience. The Playwise Framework® builds confidence, critical thinking, and academic readiness, while Emergent Curriculum adapts lessons to children's interests—making learning engaging, meaningful, and fun.</p>
  </section>

  <!-- Right panel -->
  <section class="panel panel--right">
    <svg class="shape" width="400" height="848" viewBox="0 0 400 848">
      <defs>
        <linearGradient id="playTones" x1="0" y1="0" x2="1" y2="1">
          <stop offset="0" stop-color="#c7b7a3"/>
          <stop offset=".5" stop-color="#9c8a73"/>
          <stop offset="1" stop-color="#5e8a45"/>
        </linearGradient>
      </defs>
      <path d="M0 470 C60 380 180 330 400 320 L400 848 L0 848 Z" fill="var(--sky)"/>
      <path role="img" aria-label="Photo: toddlers playing at an outdoor water table" d="M0 490 C70 400 190 352 400 350 L400 848 L0 848 Z" fill="url(#playTones)"/>
    </svg>
    <h2 class="display right-heading">Our Mission:<br>Growing Together</h2>
    <ul class="checklist checklist--mission">
      <li><svg viewBox="0 0 24 22"><path d="M2 12 L9 19 L22 3" fill="none" stroke="var(--tick)" stroke-width="4" stroke-linecap="round" stroke-linejoin="round"/></svg>Building strong partnerships – Open communication with families &amp; communities</li>
      <li><svg viewBox="0 0 24 22"><path d="M2 12 L9 19 L22 3" fill="none" stroke="var(--tick)" stroke-width="4" stroke-linecap="round" stroke-linejoin="round"/></svg>Nurturing confidence &amp; creativity – Every child is seen, heard, and supported</li>
      <li><svg viewBox="0 0 24 22"><path d="M2 12 L9 19 L22 3" fill="none" stroke="var(--tick)" stroke-width="4" stroke-linecap="round" stroke-linejoin="round"/></svg>Fostering a lifelong love for learning – Through discovery, exploration &amp; meaningful experiences</li>
    </ul>
    <p class="script right-note">As we transition to a Reggio Emilia-inspired approach, we are excited to offer a learning experience that is more engaging, dynamic, and child-centered than ever before.</p>
    <p class="welcome-box">Imagine a place where every child’s voice is heard, creativity is celebrated, and learning is an adventure—welcome to Bright Harbor!</p>
  </section>

</main>
</body>
</html>
```